Brightfield Ventures Inc. Letterhead

Creation of attractive and eye catching letterhead for a business start-up for the construction industry. Letterhead must relate to construction, but avoid standard hammer and tools in the design.

I forgot to add some details, sorry about that. Some pertinent info: Ph: 916-555-0187 brightfieldventures.example 448 Willowmere Ave, Ste 210 Folsom, CA 95999 info@brightfieldventures.example not sure if slogan should be in there" “Connecting construction professionals to create a purpose driven industry.” must be able to be used in word. Thanks!

```html
<!DOCTYPE html>
<html lang="en">
<head>
<meta charset="utf-8">
<title>Brightfield Ventures Inc. Letterhead</title>
<link rel="stylesheet" href="https://fonts.googleapis.com/css2?family=Open+Sans:wght@400;600;700&family=Lato:wght@400;700&display=swap">
<style>
  :root {
    --navy: #14205a;
    --red: #c0070d;
    --ink: #4a4a4a;
    --ink-strong: #333333;
    --paper: #ffffff;
  }
  * { margin: 0; padding: 0; box-sizing: border-box; }
  html, body { width: 1040px; height: 1200px; overflow: hidden; background: var(--paper); }
  .letterhead {
    position: relative;
    width: 1040px;
    height: 1200px;
    background: var(--paper);
    font-family: "Open Sans", sans-serif;
    color: var(--ink);
  }
  .brand {
    position: absolute;
    top: 100px;
    left: 0;
    width: 100%;
    display: flex;
    justify-content: center;
    align-items: center;
    gap: 12px;
  }
  .brand-mark { width: 20px; height: 20px; background: var(--red); }
  .brand-name {
    font-family: "Open Sans", sans-serif;
    font-weight: 700;
    font-size: 26px;
    letter-spacing: 2px;
    color: var(--navy);
    text-transform: uppercase;
  }
  .block { position: absolute; left: 97px; width: 840px; font-size: 16.5px; line-height: 20px; }
  .issue-date { top: 216px; }
  .recipient { top: 252px; line-height: 18px; }
  .salutation { top: 356px; }
  .body-para { line-height: 27px; text-align: justify; hyphens: auto; -webkit-hyphens: auto; }
  .para-1 { top: 407px; }
  .para-2 { top: 568px; }
  .para-3 { top: 677px; }
  .closing { top: 815px; }
  .signatory-name { top: 892px; font-size: 20px; line-height: 24px; font-weight: 600; color: var(--ink-strong); }
  .signatory-title { top: 923px; }
  .website {
    position: absolute;
    left: 104px;
    top: 1089px;
    font-family: "Lato", sans-serif;
    font-size: 15px;
    line-height: 20px;
    font-weight: 700;
    letter-spacing: 2.4px;
    color: var(--navy);
  }
  .website .accent { color: var(--red); }
  .footer-band { position: absolute; left: 0; top: 1122px; width: 1040px; height: 52px; }
  .footer-text {
    position: absolute;
    font-family: "Lato", sans-serif;
    font-size: 15.5px;
    line-height: 20px;
    color: #ffffff;
    white-space: nowrap;
  }
  .footer-address { left: 104px; top: 1141px; }
  .footer-contact { left: 620px; top: 1137px; }
</style>
</head>
<body>
<main class="letterhead">
  <header class="brand">
    <span class="brand-mark"></span>
    <span class="brand-name">Brightfield Ventures Inc.</span>
  </header>

  <p class="block issue-date">Issuing Date: May 5, 2018</p>
  <p class="block recipient">Name Of Employee Mr. XYZABC<br>Address of Employee<br>Address Line 2 etc..</p>
  <p class="block salutation">Dear Mr.XYZABC</p>

  <p class="block body-para para-1">Lorem Ipsum has been the industry's standard dummy text ever since the 1500s, when an unknown printer took a galley of type and scrambled it to make a type specimen book. It has survived not only five centuries, but also the leap into electronic typesetting, remaining essentially unchanged. It was popularised in the 1960s with the release of Typeline sheets containing Lorem Ipsum passages, and more recently with desktop publishing software like Pageform Studio including versions of Lorem Ipsum.</p>
  <p class="block body-para para-2">Lorem Ipsum is simply dummy text of the printing and typesetting industry. Lorem Ipsum has been the industry's standard dummy text ever since the 1500s, when an unknown printer took a galley of type and scrambled it to make a type specimen book.</p>
  <p class="block body-para para-3">It has survived not only five centuries, but also the leap into electronic typesetting, remaining essentially unchanged. It was popularised in the 1960s with the release of Typeline sheets containing Lorem IpsumIpsum passages.</p>

  <p class="block closing">Yours Sincerely</p>
  <p class="block signatory-name">Daniel Mercer</p>
  <p class="block signatory-title">Managing Director</p>

  <footer>
    <p class="website">www.<span class="accent">brightfieldventures</span>.example</p>
    <svg class="footer-band" viewBox="0 0 1040 52" aria-hidden="true">
      <polygon points="0,4 574,4 562,52 0,52" fill="var(--navy)"/>
      <polygon points="596,0 1040,0 1040,49 577,49" fill="var(--red)"/>
    </svg>
    <p class="footer-text footer-address">448 Willowmere Ave, Ste 210, Folsom, CA 95999</p>
    <p class="footer-text footer-contact">P: 916-555-0187 | E: info@brightfieldventures.example</p>
  </footer>
</main>
</body>
</html>
```